New design for www.TrimTable.com

On TrimTable you can find & book your hairdresser. TrimTable is the biggest platform in the Netherlands.

- The design should be a responcive design
- Should be able to go global, should fit in perfectly between all the big booking platforms like stayvo, ridlo etc,
- Should have te result of more bookings. :)
- We are ‘only’ asking a beautiful design, not a technical solution.
- We need a homepage (https://trimtable.com/), search resultpage ((https://trimtable.com/kapper/amsterdam/#), salonpage (https://trimtable.com/kapper/vorden/lumo-for-hair/), about us page (https://trimtable.com/aboutus/), for the hairdresser info page (https://trimtable.com/kapper/), login/register page (https://trimtable.com/account/signin/).

- On the page of the hairdresser there is a dynamic part. The part where you create your appointment. Please take a look at this part too after you choose your treatment (behandeling), employee (medewerker), Date (datum) and time (tijd). The part that you see after this, is the part where you fill in your data as a consumer.

I've added more logo's but mostly we use the green color.

A few of our competitors: www.plumsalo.com, www.korifex.com

Target Market(s)

All consumers

Industry/Entity Type

Hair And Beauty

Number of Pages Required

5+ page

Font styles to use
Sans Serif

Colors
abd036
c3c3c3
757575

Requirements
Must have
• Responsive
• We did an A/B test with the homepage. It turns out that option B works better then option A (take a look at the uploaded pictures). So what we need on the homepage: The USP's with the green checkboxes, The search button needs to by dynamic (changes for example from light green to dark green so you can see you can click it) The call to action sentence Zoek & Vind je kapsalon, the searchfield and searchbutton should be seperated.
Nice to have
• The style that we like is the flat design style. The website should be simple, clean and it should feel a bit like a luxury thing. Because an appointment with the hairdresser can be a real treat and luxury moment for yourself.
• The luxury feeling and flat design that is in the www.ridlo.com website is really nice for example. But then it has to be a bit more light and not so black and dark.

```html
<!DOCTYPE html>
<html lang="nl">
<head>
<meta charset="utf-8">
<title>TrimTable – Zoek &amp; vind je kapsalon</title>
<link rel="stylesheet" href="https://fonts.googleapis.com/css2?family=Open+Sans:wght@400;600;700;800&display=swap">
<style>
:root{
  --green:#abd036;
  --green-dark:#8db21f;
  --orange:#f5a623;
  --grey-light:#c3c3c3;
  --grey:#757575;
  --ink:#333333;
  --dark:#2b2b2b;
  --darker:#222222;
  --white:#ffffff;
}
*{box-sizing:border-box;margin:0;padding:0}
html,body{width:1200px;height:2740px;overflow:hidden}
body{font-family:"Open Sans",Arial,sans-serif;color:var(--ink);background:var(--white)}
a{color:inherit;text-decoration:none}
section,header,footer{overflow:hidden}

/* Hero */
.hero{position:relative;height:650px;color:var(--white)}
.hero-photo{position:absolute;inset:0;background:radial-gradient(ellipse at 50% 40%,#5a5048 0%,#3b342f 45%,#1f1c1a 100%)}
.hero-shade{position:absolute;inset:0;background:rgba(0,0,0,.25)}
.nav{position:relative;display:flex;justify-content:space-between;align-items:center;padding:26px 60px 0 56px}
.brand{display:flex;align-items:center;gap:10px;font-weight:700;font-size:26px;color:var(--green)}
.brand-dot{width:22px;height:22px;border-radius:50%;background:var(--green)}
.menu{display:flex;align-items:center;gap:34px;font-size:12px;font-weight:600;letter-spacing:.5px;text-transform:uppercase}
.menu .btn-outline{border:1px solid var(--white);border-radius:16px;padding:7px 20px}
.menu .btn-outline + .btn-outline{margin-left:-16px}
.hero-title{position:relative;text-align:center;margin-top:120px;font-size:34px;font-weight:800;letter-spacing:1px}
.usps{position:relative;display:flex;justify-content:center;gap:32px;margin-top:14px;font-size:14px}
.usps li{list-style:none;display:flex;align-items:center;gap:7px}
.search{position:relative;display:flex;justify-content:center;gap:10px;margin-top:54px}
.search-field{width:340px;height:42px;border-radius:21px;background:var(--white);color:var(--grey);font-size:13px;padding:0 20px;display:flex;align-items:center}
.search-button{width:130px;height:42px;border-radius:21px;background:var(--orange);color:var(--white);font-size:13px;font-weight:700;display:flex;align-items:center;justify-content:center}

/* Sections */
.section-title{text-align:center;font-size:30px;font-weight:700;text-transform:uppercase;color:var(--ink);line-height:36px}
.section-lead{width:760px;margin:14px auto 0;text-align:center;font-size:13px;line-height:1.7;color:var(--grey)}
.welcome{height:236px;padding-top:60px}

/* Stats */
.stats{height:384px;background:linear-gradient(#2e2e2e,#3c3c3c);color:var(--white);padding-top:70px}
.stats-title{text-align:center;color:var(--green);font-size:24px;font-weight:700;text-transform:uppercase}
.stats-row{display:flex;justify-content:space-between;width:1060px;margin:56px auto 0}
.stat{width:220px}
.stat-label{font-size:21px;font-weight:700;text-transform:uppercase;line-height:1.25}
.stat-value{font-size:56px;font-weight:700;color:var(--orange);margin-top:8px;line-height:1.1}

/* Styles grid */
.styles{height:840px;padding-top:50px}
.style-grid{display:grid;grid-template-columns:repeat(3,1fr);grid-template-rows:330px 330px;width:1000px;margin:40px auto 0}
.style-card{position:relative;overflow:hidden}
.style-photo{position:absolute;inset:0}
.tone-a{background:linear-gradient(135deg,#d9d5cf,#8a7f76)}
.tone-b{background:linear-gradient(135deg,#e7e2dc,#5d534c)}
.tone-c{background:linear-gradient(135deg,#7d6e62,#2e2824)}
.tone-d{background:linear-gradient(135deg,#3a3a3a,#101010)}
.tone-e{background:linear-gradient(135deg,#c9c4bf,#4d4641)}
.caption{position:absolute;left:0;right:0;bottom:0;background:rgba(171,208,54,.92);color:var(--white);padding:14px 22px 12px}
.caption-title{font-size:17px;font-weight:700;text-transform:uppercase}
.caption-link{font-size:10px;font-weight:600;text-transform:uppercase;margin-top:3px}
.feature-card{background:var(--green);color:var(--white);padding:34px 28px}
.feature-card .caption-title{font-size:19px}
.feature-card p{font-size:13px;line-height:1.7;margin-top:14px}
.feature-card .caption-link{margin-top:16px}

/* Newsletter */
.newsletter{height:280px;padding-top:64px}
.signup{display:flex;justify-content:center;gap:10px;margin-top:30px}
.signup-field{width:330px;height:40px;border:1px solid var(--grey-light);border-radius:20px;padding:0 20px;display:flex;align-items:center;font-size:13px;color:var(--grey)}
.signup-button{width:120px;height:40px;border-radius:20px;background:var(--orange);color:var(--white);font-size:12px;font-weight:700;display:flex;align-items:center;justify-content:center}

/* Footer */
.footer{height:310px;background:var(--dark);color:var(--grey-light);display:flex;padding:46px 100px 0}
.footer-col h4{color:var(--white);font-size:13px;font-weight:700;text-transform:uppercase;line-height:1.55}
.footer-about{width:420px}
.footer-about p{font-size:11.5px;line-height:1.7;margin-top:14px;width:330px}
.footer-about .more{display:block;margin-top:14px;font-size:11px;font-weight:700;color:var(--white);text-transform:uppercase}
.footer-links{width:360px}
.link-cols{display:flex;gap:70px;margin-top:16px}
.link-cols ul{list-style:none;font-size:11.5px;line-height:2.05}
.footer-follow p{font-size:11.5px;margin-top:12px}
.socials{display:flex;gap:8px;margin-top:12px}
.socials span{width:26px;height:26px;border-radius:50%;background:#666}
.footer-brand{display:flex;align-items:center;gap:8px;margin-top:26px;font-size:22px;font-weight:700;color:var(--white)}
.footer-brand .brand-dot{width:18px;height:18px}
.legal{height:40px;background:var(--darker);color:var(--grey);font-size:11px;display:flex;align-items:center;justify-content:center;gap:26px}
</style>
</head>
<body>

<header class="hero">
  <div class="hero-photo" role="img" aria-label="Kappersgereedschap: scharen, kammen en tondeuses op een donkere houten ondergrond"></div>
  <div class="hero-shade"></div>
  <nav class="nav">
    <a class="brand" href="#"><span class="brand-dot"></span>TrimTable</a>
    <div class="menu">
      <a href="#">About us</a>
      <a href="#">Services</a>
      <a href="#">Styles</a>
      <a class="btn-outline" href="#">Login</a>
      <a class="btn-outline" href="#">Register</a>
    </div>
  </nav>
  <h1 class="hero-title">ZOEK &amp; VIND JE KASALON</h1>
  <ul class="usps">
    <li><svg width="14" height="14" viewBox="0 0 14 14"><path d="M2 7.5l3 3 7-7" fill="none" stroke="#abd036" stroke-width="2.4"/></svg>Grootste kappersboekingsite van NL</li>
    <li><svg width="14" height="14" viewBox="0 0 14 14"><path d="M2 7.5l3 3 7-7" fill="none" stroke="#abd036" stroke-width="2.4"/></svg>Afspraken zijn 100% zeker</li>
    <li><svg width="14" height="14" viewBox="0 0 14 14"><path d="M2 7.5l3 3 7-7" fill="none" stroke="#abd036" stroke-width="2.4"/></svg>Meer dan 20.000 kappers reviews</li>
  </ul>
  <div class="search">
    <div class="search-field">Zoek op plaats of postcode</div>
    <a class="search-button" href="#">ZOEKEN</a>
  </div>
</header>

<section class="welcome">
  <h2 class="section-title">Welcome TrimTable</h2>
  <p class="section-lead">Lorem Ipsum is simply dummy text of the printing and typesetting industry. Lorem Ipsum has been the industry's standard dummy text ever since the 1500s, when an unknown printer took a galley of type and scrambled it to make a type specimen book.</p>
</section>

<section class="stats">
  <h3 class="stats-title">Laatste afspraak gemaakt op 16 oktober 2015 om 11:09</h3>
  <div class="stats-row">
    <div class="stat"><div class="stat-label">Behandelingen<br>te boeken</div><div class="stat-value">16.375</div></div>
    <div class="stat"><div class="stat-label">Afspraken<br>gemaakt</div><div class="stat-value">571.278</div></div>
    <div class="stat"><div class="stat-label">Kappers te<br>boeken</div><div class="stat-value">7.171</div></div>
    <div class="stat"><div class="stat-label">Betrouwbare<br>reviews</div><div class="stat-value">26.596</div></div>
  </div>
</section>

<section class="styles">
  <h2 class="section-title">Latest Styles</h2>
  <p class="section-lead">Lorem Ipsum is simply dummy text of the printing and typesetting industry. Lorem Ipsum has been the industry's standard dummy.</p>
  <div class="style-grid">
    <article class="style-card feature-card">
      <div class="caption-title">Lorem ipsum is simply</div>
      <p>Een frisse coupe voor het nieuwe seizoen. Onze stylisten laten zien hoe je met een strakke fade en een natuurlijke lengte bovenop een moderne, verzorgde look neerzet die elke dag makkelijk te stylen is, met weinig product en veel effect.</p>
      <div class="caption-link">Click here for more »</div>
    </article>
    <article class="style-card">
      <div class="style-photo tone-a" role="img" aria-label="Zwart-witfoto van een man bij de kapper"></div>
      <div class="caption"><div class="caption-title">Lorem ipsum is simply</div><div class="caption-link">Click here for more »</div></div>
    </article>
    <article class="style-card">
      <div class="style-photo tone-b" role="img" aria-label="Kapper knipt het haar van een klant met een tondeuse"></div>
      <div class="caption"><div class="caption-title">Lorem ipsum is simply</div><div class="caption-link">Click here for more »</div></div>
    </article>
    <article class="style-card">
      <div class="style-photo tone-c" role="img" aria-label="Close-up van een verzorgde baard"></div>
      <div class="caption"><div class="caption-title">Lorem ipsum is simply</div><div class="caption-link">Click here for more »</div></div>
    </article>
    <article class="style-card">
      <div class="style-photo tone-d" role="img" aria-label="Man in pak met gestyled kort haar"></div>
      <div class="caption"><div class="caption-title">Lorem ipsum is simply</div><div class="caption-link">Click here for more »</div></div>
    </article>
    <article class="style-card">
      <div class="style-photo tone-e" role="img" aria-label="Portret van een man met een modern kapsel"></div>
      <div class="caption"><div class="caption-title">Lorem ipsum is simply</div><div class="caption-link">Click here for more »</div></div>
    </article>
  </div>
</section>

<section class="newsletter">
  <h2 class="section-title">Latest Styles</h2>
  <p class="section-lead">Lorem Ipsum is simply dummy text of the printing and typesetting industry. Lorem Ipsum has been the industry's standard dummy text ever since the 1500s, when an unknown printer took a galley of type and scrambled it to make a type specimen book.</p>
  <div class="signup">
    <div class="signup-field">Enter your email</div>
    <a class="signup-button" href="#">SUBSCRIBE</a>
  </div>
</section>

<footer class="footer">
  <div class="footer-col footer-about">
    <h4>Maak een afspraak bij de kapper<br>in een van deze plaatsen.</h4>
    <p>Vind een kapper bij jou in de buurt, vergelijk prijzen en lees reviews van andere klanten. Boek direct online, dag en nacht, en ontvang meteen een bevestiging.</p>
    <a class="more" href="#">Read more »</a>
  </div>
  <div class="footer-col footer-links">
    <h4>Welcome</h4>
    <div class="link-cols">
      <ul><li>Kapper Amsterdam</li><li>Kapper Rotterdam</li><li>Kapper Den Haag</li><li>Kapper Utrecht</li><li>Kapper Eindhoven</li><li>Kapper Tilburg</li></ul>
      <ul><li>Kapper Groningen</li><li>Kapper Almere</li><li>Kapper Breda</li><li>Kapper Nijmegen</li><li>Kapper Enschede</li><li>Kapper Haarlem</li></ul>
    </div>
  </div>
  <div class="footer-col footer-follow">
    <h4>Follow us</h4>
    <p>Connect with us on social</p>
    <div class="socials"><span></span><span></span><span></span><span></span><span></span></div>
    <div class="footer-brand"><span class="brand-dot"></span>TrimTable</div>
  </div>
</footer>
<div class="legal">
  <span>© 2015 TrimTable. All rights reserved.</span>
  <span>Terms &amp; Conditions</span>
  <span>Privacy policy</span>
  <span>Contact</span>
</div>

</body>
</html>
```